Blood Sugar WordPress Redesign

IMPORTANT: the design will need to look nice on mobile...so please keep that in mind!
We need to redesign our current Wordpress page to make it more appealing and look like an ecommerce page. We need the ability to implement this design on our Wordpress site.
Here is the current page: https://www.kplarewellness.com/supplements/vital-prime-daily/
However, the reference sample of what it has to look like or complement is also attached.
Attached is the Word document is the copy for the new page and the FAQs text.
The color palette for the page is attached also.
Thanks!

```html
<!DOCTYPE html>
<html lang="en">
<head>
<meta charset="utf-8">
<title>Vital Prime Daily – Landing Page</title>
<link href="https://fonts.googleapis.com/css2?family=Outfit:wght@300;400;500;600;700&family=Lora:wght@500&display=swap" rel="stylesheet">
<style>
:root{
  --stage:#a7a7a7;
  --blue:#4656d0;
  --blue-deep:#2b3bb5;
  --blue-soft:#6f84ec;
  --blue-mid:#4b60e0;
  --navy:#16205e;
  --ink:#1b1b28;
  --muted:#55576a;
  --lav:#eef0fc;
  --lav-2:#dfe3fb;
  --white:#ffffff;
  --gold:#e7b325;
}
*{box-sizing:border-box;margin:0;padding:0}
html,body{width:811px;height:1200px;overflow:hidden}
body{background:var(--stage);font-family:"Outfit",sans-serif;color:var(--ink);position:relative}
.column{position:absolute;top:78px;width:203px;background:var(--white);overflow:hidden}
.col-left{left:61px;height:1049px}
.col-mid{left:304px;height:791px}
.col-right{left:547px;height:946px}
.section{position:absolute;left:0;width:203px;overflow:hidden}
.a{position:absolute}
.c{left:0;width:203px;text-align:center}
.h2{font-size:8.6px;font-weight:600;line-height:1.2;color:var(--ink);z-index:2}
.h2 .hl,.hl{color:var(--blue)}
.rule{position:absolute;height:1px;width:22px;background:var(--blue);left:90px;z-index:2}
.p{font-size:3.2px;line-height:1.45;color:var(--muted);z-index:2}
.btn{position:absolute;background:var(--blue);color:#fff;border-radius:8px;font-size:3.4px;font-weight:600;display:flex;align-items:center;justify-content:center;letter-spacing:.1px;z-index:2}
.btn.dark{background:var(--blue-deep)}
.list-title{font-size:3.6px;font-weight:600;color:var(--blue);z-index:2}
.item{position:absolute;padding-left:7px;z-index:2}
.item::before{content:"";position:absolute;left:0;top:.6px;width:2.6px;height:2.6px;border-radius:50%;border:.7px solid var(--blue)}
.on-blue .item::before{border-color:#fff}
.item b{font-size:3.4px;font-weight:600;color:var(--blue);display:block}
.on-blue .item b{color:#fff}
.photo{position:absolute;background:linear-gradient(150deg,#6b5347,#2e2420 70%)}
.photo-round{border-radius:50%;border:3px solid #fff;box-shadow:0 0 0 5px rgba(70,86,208,.18),0 0 0 10px rgba(70,86,208,.09)}
.thumb{position:absolute;border-radius:4px;background:linear-gradient(160deg,#c9b8a8,#5d4636)}
.play{position:absolute;left:22px;top:26px;width:12px;height:12px;border-radius:50%;border:1px solid #fff}
.play::after{content:"";position:absolute;left:4px;top:2.6px;border-left:4px solid #fff;border-top:2.6px solid transparent;border-bottom:2.6px solid transparent}
.arrows{position:absolute;left:90px;display:flex;gap:3px}
.arrows span{width:10px;height:10px;border-radius:50%;background:var(--lav-2);color:var(--blue);font-size:5px;display:flex;align-items:center;justify-content:center}
.arrows span+span{background:var(--blue);color:#fff}
.logo{font-weight:700;color:var(--ink);letter-spacing:.3px}
.on-blue{background:var(--blue);color:#fff}
.on-blue .p{color:#e6e9ff}
.card-month{position:absolute;left:33px;width:137px;border-radius:4px;color:#fff;text-align:center}
.card-month .badge{position:absolute;left:56px;top:-12px;width:24px;height:24px;border-radius:50%;background:inherit;border:1px solid #fff;font-size:3.6px;line-height:1.15;display:flex;align-items:center;justify-content:center;flex-direction:column}
.card-month h4{font-size:4px;font-weight:500;margin-top:16px}
.card-month p{font-size:2.9px;line-height:1.4;margin:5px 14px 0;color:#e9ecff}
.faq-row{position:absolute;left:90px;width:95px;height:7px;border:.5px solid var(--lav-2);border-radius:1px;font-size:2.4px;color:var(--ink);padding:1.6px 3px;background:#fff}
.faq-row::after{content:"";position:absolute;right:3px;top:2px;width:2.5px;height:2.5px;border-radius:50%;background:var(--blue)}
.review-card{position:absolute;width:57px;height:86px;background:#fff;border-radius:3px;box-shadow:0 1px 3px rgba(30,40,120,.15);overflow:hidden}
.review-card .shot{height:45px;background:linear-gradient(160deg,#b79f8c,#3a2c26)}
.review-card p{font-size:2.2px;line-height:1.4;text-align:center;padding:3px;color:var(--ink)}
.nav-link{font-size:2.2px;color:var(--ink);position:absolute;top:13px}
</style>
</head>
<body>

<main class="column col-left">

  <header class="section" style="top:0;height:23px">
    <div class="a logo" style="left:11px;top:8px;font-size:6.5px">KPLARE</div>
    <span class="nav-link" style="left:76px;color:var(--blue);text-decoration:underline">HOME</span>
    <span class="nav-link" style="left:91px">SUCCESS STORIES</span>
    <span class="nav-link" style="left:119px">MEDIA ROOM</span>
    <span class="nav-link" style="left:143px">ABOUT</span>
    <span class="nav-link" style="left:159px">BLOGS</span>
    <span class="nav-link" style="left:176px">CONTACT US</span>
    <div class="btn" style="left:148px;top:5px;width:24px;height:5px;background:var(--blue-soft);font-size:2.3px">KP's Products</div>
    <div class="btn dark" style="left:173px;top:5px;width:20px;height:5px;font-size:2.3px">Login</div>
  </header>

  <section class="section" style="top:23px;height:126px;background:linear-gradient(90deg,#f3f3f5,#dcdce0)">
    <div class="a" style="left:96px;top:14px;width:100px;height:100px;border-radius:50%;background:radial-gradient(circle,#fff 52%,#cdd3fb 53%,#aab4f4 70%,#dfe3fb 71%)"></div>
    <div class="a" role="img" aria-label="Three bottles of Vital Prime Daily supplement" style="left:104px;top:36px;width:86px;height:60px;border-radius:6px;background:linear-gradient(180deg,#fafafa,#dfe2f5 60%,#3f4fc3 61%,#2b3bb5)"></div>
    <div class="a" style="left:11px;top:20px;font-size:13.5px;font-weight:500;color:var(--blue);z-index:2">Vital Prime</div>
    <div class="a" style="left:11px;top:33px;font-size:20px;font-weight:600;color:var(--ink);z-index:2">Daily</div>
    <div class="a" style="left:11px;top:59px;width:76px;font-size:4.4px;line-height:1.25">The Natural Way to Boost GLP-1 Levels to Support Fat Loss Control Hunger and Reduce Food Cravings</div>
    <div class="btn dark" style="left:11px;top:89px;width:47px;height:14px;font-size:3.6px">BUY NOW</div>
  </section>

  <section class="section" style="top:149px;height:201px">
    <div class="a c h2" style="top:15px;font-size:8.2px">Struggling with stubborn weight gain,<br>energy crashes, or blood sugar spikes?</div>
    <div class="a c" style="top:39px;font-size:6.8px;color:var(--blue)">Vital Prime Daily is here to help!</div>
    <div class="a" style="top:50px;left:36px;width:131px;text-align:center;font-size:4.3px;line-height:1.2">This advanced formula helps stabilize blood sugar, control cravings, and support a healthier weight—so you feel energized and in control all day</div>
    <div class="rule" style="top:72px"></div>
    <div class="photo photo-round" role="img" aria-label="Smiling woman in a pink blazer holding a bottle" style="left:-30px;top:80px;width:100px;height:120px;border-radius:50%;background:linear-gradient(160deg,#e0e0e6 35%,#d2158d 36%,#8b0d5e)"></div>
    <div class="a list-title" style="left:83px;top:79px;width:115px;font-size:4.6px;line-height:1.2">Clinically-Studied Ingredients for Natural Weight Loss designed:</div>
    <div class="item p" style="left:85px;top:94px;width:115px"><span class="hl">Naturally increase GLP-1 levels</span> (with clinically-tested ingredients) so you eat less and stay full longer, reducing appetite</div>
    <div class="item p" style="left:85px;top:106px;width:115px"><span class="hl">Support fat loss, accelerate fat burning and reduce body weight</span> including visceral (belly) fat, when combined with a healthy lifestyle (Lose Fat, Not Muscle)*</div>
    <div class="item p" style="left:85px;top:123px;width:115px">By boosting GLP-1, your body sends signals to the brain that <span class="hl">reduce cravings, quiet food noise</span>, and help you feel full longer—naturally.*</div>
    <div class="item p" style="left:85px;top:140px;width:115px"><span class="hl">For anyone who wants fast, healthy weight loss</span> as well as for diabetics, pre-diabetics, and those with insulin resistance*</div>
    <div class="item p" style="left:85px;top:152px;width:115px">Support <span class="hl">healthy blood sugar levels</span> to prevent your body from storing fat and to reduce food cravings, especially for carbs and sugar</div>
    <div class="btn dark" style="left:85px;top:175px;width:37px;height:11px;font-size:3px">BUY NOW</div>
  </section>

  <section class="section" style="top:350px;height:155px">
    <div class="a c h2" style="top:12px;font-size:10px">Real Women<br><span class="hl">Real Results</span></div>
    <div class="rule" style="top:40px"></div>
    <div class="thumb" role="img" aria-label="Woman with glasses holding a supplement bottle" style="left:13px;top:56px;width:57px;height:64px"></div>
    <div class="thumb" role="img" aria-label="Woman with curly hair holding a bottle" style="left:75px;top:56px;width:57px;height:64px"></div>
    <div class="thumb" role="img" aria-label="Smiling woman beside a supplement bottle" style="left:136px;top:56px;width:57px;height:64px"></div>
    <div class="arrows" style="top:130px"><span>←</span><span>→</span></div>
  </section>

  <section class="section" style="top:505px;height:353px;background:var(--lav)">
    <div class="a c h2" style="top:14px">Powerful Ingredients<br><span class="hl">Backed by Science</span></div>
    <div class="rule" style="top:41px"></div>
    <div class="a list-title" style="left:11px;top:56px;font-size:5px">The Power of Citrolin®</div>
    <div class="a p" style="left:11px;top:63px;width:125px">Citrolin® is a patented citrus flavonoid blend that has been clinically studied for its impact on blood sugar regulation, insulin function, and overall metabolic health. Research suggests that Citrolin® supports glucose metabolism by:</div>
    <div class="photo photo-round" role="img" aria-label="Smiling woman holding a bottle" style="left:117px;top:77px;width:84px;height:84px"></div>
    <div class="item p" style="left:15px;top:85px;width:100px"><b>Boosting GLP-1 Levels</b>Citrolin® has been shown to increase GLP-1, a hormone that plays a crucial role in blood sugar regulation and appetite control.</div>
    <div class="item p" style="left:15px;top:101px;width:100px"><b>Reducing Fasting Blood Sugar</b>Clinical studies indicate that Citrolin® helps maintain blood glucose levels within a healthy range, making it a promising solution for balance.</div>
    <div class="item p" style="left:15px;top:123px;width:100px"><b>Enhancing Insulin Sensitivity</b>By promoting normal insulin function, Citrolin® may support efficient glucose uptake, helping the body use energy more effectively.</div>
    <div class="item p" style="left:15px;top:146px;width:100px"><b>Lowering Inflammation</b>High blood sugar levels can contribute to oxidative stress and inflammation, but research suggests that Citrolin® helps combat these effects.</div>
    <div class="a p" style="left:11px;top:171px;width:115px;font-style:italic;font-size:2.6px"><span class="hl">Reference:</span> Moreno, A., Tavares, L., &amp; Reis, D. (2019). Effectiveness of Citrolin® in managing hyperglycemia and reversal of prediabetes condition: A double-blind, randomized, controlled study.</div>

    <figure class="a" style="left:36px;top:192px;width:130px;height:140px;border-radius:8px;background:#c9d3ec">
      <div class="a" style="left:9px;top:6px;width:112px;height:24px;border-radius:12px;background:#fff;border:.7px solid var(--navy);font-family:'Lora',serif;font-size:5.4px;text-align:center;line-height:1.3;padding-top:4px">Citrolin® Increases GLP-1 Levels<br>in Clinical Study</div>
      <svg class="a" style="left:0;top:34px" width="130" height="104" viewBox="0 0 130 104" font-family="Outfit,sans-serif">
        <rect x="33" y="3" width="3" height="3" fill="#7f98d8"/><text x="38" y="6" font-size="2.6" fill="#1b1b28">Placebo</text>
        <rect x="68" y="3" width="3" height="3" fill="#16205e"/><text x="73" y="6" font-size="2.6" fill="#1b1b28">Citrolin® 200 mg</text>
        <g stroke="#9fb0dc" stroke-width=".4">
          <line x1="14" y1="14" x2="125" y2="14"/><line x1="14" y1="33" x2="125" y2="33"/><line x1="14" y1="52" x2="125" y2="52"/><line x1="14" y1="71" x2="125" y2="71"/>
        </g>
        <g font-size="2.6" fill="#1b1b28"><text x="5" y="15">20%</text><text x="5" y="34">10%</text><text x="6" y="53">0%</text><text x="3" y="72">-10%</text></g>
        <rect x="27" y="48" width="14" height="4" fill="#7f98d8"/>
        <rect x="43" y="19" width="14" height="33" rx="2" fill="#16205e"/>
        <rect x="79" y="52" width="14" height="9" fill="#7f98d8"/>
        <rect x="95" y="10" width="14" height="42" rx="2" fill="#16205e"/>
        <path d="M50 28l1 3 3 1-3 1-1 3-1-3-3-1 3-1z M102 18l1 3 3 1-3 1-1 3-1-3-3-1 3-1z" fill="#fff"/>
        <g font-size="2.6" fill="#1b1b28"><text x="30" y="56">+0.2%</text><text x="47" y="56">17%</text><text x="99" y="56">22%</text><text x="84" y="65">-5%</text></g>
        <g font-size="2.8" font-weight="600" fill="#16205e"><text x="35" y="80">STUDY 1</text><text x="88" y="80">STUDY 2</text></g>
        <text x="65" y="90" font-size="1.9" fill="#333" text-anchor="middle">Source: results showed a 6% decrease in hyperglycemia and a 22% increase in GLP-1</text>
        <text x="65" y="93" font-size="1.9" fill="#333" text-anchor="middle">blood levels compared to the placebo group over 12 weeks.</text>
      </svg>
    </figure>
  </section>

  <section class="section" style="top:858px;height:191px">
    <div class="a" style="left:122px;top:62px;width:96px;height:96px;border-radius:50%;background:radial-gradient(circle,#fff 40%,#c6cdf8 60%,#eef0fc 61%)"></div>
    <div class="a" role="img" aria-label="Open bottle of Vital Prime Daily with capsules" style="left:142px;top:84px;width:36px;height:52px;border-radius:5px;background:linear-gradient(180deg,#fafafa 45%,#2b3bb5 46%)"></div>
    <div class="a c h2" style="top:16px">Other Key Ingredients for<br><span class="hl">Comprehensive Blood Sugar Support</span></div>
    <div class="rule" style="top:42px"></div>
    <div class="item p" style="left:11px;top:54px;width:112px"><b>Cinnamon Bark – Nature's Blood Sugar Balancer</b>Cinnamon has been widely studied for its ability to help regulate blood sugar levels. It works by improving insulin sensitivity, allowing your body to use glucose more efficiently. It also helps slow carbohydrate digestion, reducing post-meal blood sugar spikes.</div>
    <div class="item p" style="left:11px;top:84px;width:112px"><b>Chromium Picolinate – Essential for Insulin Function</b>Chromium is a vital trace mineral that plays a key role in carbohydrate and lipid metabolism. As chromium picolinate, it enhances insulin's effectiveness, helping cells absorb glucose more efficiently and reduce cravings.</div>
    <div class="item p" style="left:11px;top:116px;width:112px"><b>Alpha-Lipoic Acid – A Potent Antioxidant for Glucose Metabolism</b>Alpha-Lipoic Acid is a powerful antioxidant known for its role in improving insulin sensitivity. It helps transport glucose into cells, reducing blood sugar levels and supporting healthy nerve function.</div>
    <div class="a p" style="left:17px;top:160px;width:108px">Together, these ingredients create a well-rounded formula designed to promote stable blood sugar levels, support fat loss, and help control cravings—empowering you to take control of your health.</div>
  </section>
</main>

<main class="column col-mid">

  <section class="section on-blue" style="top:0;height:168px">
    <div class="photo" role="img" aria-label="Smiling woman holding a bottle of Vital Prime Daily" style="left:122px;top:18px;width:128px;height:128px;border-radius:50%;border:3px solid #7f8ff0;background:linear-gradient(160deg,#e8e8ee 30%,#3b2a22 31%,#18120f)"></div>
    <div class="a" style="left:11px;top:13px;font-size:8.6px;font-weight:600;z-index:2">Who Is Vital Prime Daily For?</div>
    <div class="a" style="left:11px;top:28px;width:22px;height:1px;background:#fff"></div>
    <div class="a p" style="left:11px;top:39px;width:105px">Whether you are managing specific health concerns or striving for overall wellness, this formula provides targeted support.</div>
    <div class="item p" style="left:12px;top:53px;width:108px"><b>Individuals Seeking Healthy Weight Management</b>Balanced blood sugar levels play a role in metabolism and fat storage, designed to help maintain normal glucose levels as part of a balanced lifestyle</div>
    <div class="item p" style="left:12px;top:80px;width:108px"><b>Those Looking to Support Blood Sugar Balance</b>Fluctuations in blood sugar can impact energy, cravings, and overall well-being. Key ingredients support glucose metabolism and insulin function within the normal range</div>
    <div class="item p" style="left:12px;top:107px;width:108px"><b>Anyone Looking for Sustained Energy &amp; Fewer Cravings</b>A balanced blood sugar response can help prevent energy crashes and sugar cravings, to promote stable energy levels throughout the day.</div>
    <div class="item p" style="left:12px;top:130px;width:108px"><b>Individuals with Dietary &amp; Lifestyle Concerns</b>If you are mindful of carbohydrate intake, energy levels, or sugar cravings, it provides nutritional support to complement a healthy diet and active lifestyle.</div>
  </section>

  <section class="section" style="top:168px;height:166px;background:var(--lav)">
    <div class="a c h2" style="top:25px">Why Customers Love<br><span class="hl">Vital Prime Daily</span></div>
    <div class="rule" style="top:52px"></div>
    <div class="thumb" role="img" aria-label="Video: customer holding a bottle" style="left:12px;top:68px;width:57px;height:64px"><span class="play"></span></div>
    <div class="thumb" role="img" aria-label="Video: customer outdoors with product" style="left:74px;top:68px;width:57px;height:64px;background:linear-gradient(160deg,#ddd3c7,#7b6250)"><span class="play"></span></div>
    <div class="thumb" role="img" aria-label="Video: customer in white hoodie" style="left:135px;top:68px;width:57px;height:64px;background:linear-gradient(160deg,#e8e4e0,#8e7a6a)"><span class="play"></span></div>
    <div class="arrows" style="top:144px"><span>←</span><span>→</span></div>
  </section>

  <section class="section" style="top:334px;height:105px">
    <svg class="a" style="left:0;top:0" width="203" height="105" viewBox="0 0 203 105" font-family="Outfit,sans-serif">
      <path d="M18 30 A18 18 0 0 1 54 30 L54 64 A16 16 0 0 0 86 64 L86 30 A16 16 0 0 1 118 30 L118 64 A16 16 0 0 0 150 64 L150 30 A16 16 0 0 1 182 30" fill="none" stroke="#2b3bb5" stroke-width=".8"/>
      <g fill="#fff" stroke="#2b3bb5" stroke-width=".8">
        <circle cx="36" cy="30" r="12"/><circle cx="70" cy="64" r="12"/><circle cx="102" cy="30" r="12"/><circle cx="134" cy="64" r="12"/><circle cx="166" cy="30" r="12"/>
      </g>
      <g fill="none" stroke="#2b3bb5" stroke-width=".7">
        <rect x="31" y="27" width="10" height="5" rx="2.5" transform="rotate(-30 36 30)"/>
        <rect x="66" y="59" width="8" height="10" rx="1"/><line x1="66" y1="62" x2="74" y2="62"/>
        <path d="M96 26l3 4-3 4M108 26l-3 4 3 4M99 30h6"/>
        <path d="M130 60l4-2 4 2v5l-4 2-4-2z"/>
        <path d="M166 24c3 4 4 6 4 8a4 4 0 0 1-8 0c0-2 1-4 4-8z"/>
      </g>
      <g font-size="3.3" fill="#1b1b28" text-anchor="middle" font-weight="500">
        <text x="36" y="49">Naturally</text><text x="36" y="53">Boost</text><text x="36" y="57">GLP-1 Levels*</text>
        <text x="70" y="37">Naturally Feel</text><text x="70" y="41">Full Faster</text><text x="70" y="45">&amp; Stay</text><text x="70" y="49">Full Longer*</text>
        <text x="102" y="49">Reduce Food</text><text x="102" y="53">Cravings</text><text x="102" y="57">and Overall</text><text x="102" y="61">Appetite*</text>
        <text x="134" y="40">Maximize Fat</text><text x="134" y="44">Burning</text><text x="134" y="48">in the Body*</text>
        <text x="166" y="49">Manage</text><text x="166" y="53">Blood Sugar</text><text x="166" y="57">Levels*</text>
      </g>
    </svg>
  </section>

  <section class="section on-blue" style="top:439px;height:172px">
    <div class="a c" style="top:14px;font-size:8.6px;font-weight:500;line-height:1.3">Take Control of Your<br>Vital Prime Daily &amp; Metabolism Today!</div>
    <div class="a" style="left:90px;top:40px;width:22px;height:1px;background:#fff"></div>
    <div class="photo" role="img" aria-label="Woman with blue glasses holding a bottle" style="left:-10px;top:56px;width:80px;height:80px;border-radius:50%;border:3px solid #8c9bf3;box-shadow:0 0 0 8px rgba(255,255,255,.1)"></div>
    <div class="a p" style="left:83px;top:53px;width:110px">Don't let unstable blood sugar hold you back. Whether you're looking to support fat loss, curb cravings, support healthy blood sugar levels or boost your metabolism, we are here to help.</div>
    <div class="item" style="left:86px;top:76px;font-size:3.8px">Promote healthy weight loss and support fat loss</div>
    <div class="item" style="left:86px;top:86px;font-size:3.8px">Support normal insulin function</div>
    <div class="item" style="left:86px;top:96px;font-size:3.8px">Manage sugar cravings &amp; energy crashes</div>
    <div class="a" style="left:83px;top:109px;font-size:8.8px;color:#bfc8ff;font-weight:500">Ready to feel your best?</div>
    <div class="a" style="left:83px;top:122px;width:110px;font-size:5.4px;line-height:1.3">Try Vital Prime Daily today and experience the difference!</div>
    <div class="btn" style="left:83px;top:148px;width:47px;height:13px;background:var(--navy);font-size:3.6px">ORDER NOW</div>
  </section>

  <section class="section" style="top:611px;height:180px">
    <div class="a c h2" style="top:20px">Why Customers Love<br><span class="hl">Loving Their Results</span></div>
    <div class="rule" style="top:47px"></div>
    <article class="review-card" style="left:12px;top:59px"><div class="shot" role="img" aria-label="Before and after photos of a customer"></div><p>Ana lost 48 pounds and feels amazing. She says: "I do low carb and focus mainly on lean meats and veggies, and I don't have sugar cravings anymore, especially for ice cream."</p></article>
    <article class="review-card" style="left:74px;top:59px"><div class="shot" role="img" aria-label="Before and after photos of a customer in a colorful dress" style="background:linear-gradient(160deg,#d98b3a,#3a2c26)"></div><p>Rena lost 71 pounds, lowered her A1C and is no longer diabetic. She says: "I started my journey with intermittent fasting and smoothies. Knowing that I achieved something great, I kept going!"</p></article>
    <article class="review-card" style="left:135px;top:59px"><div class="shot" role="img" aria-label="Before and after photos of a customer"></div><p>Dana says: "I'm back at my desired weight. Everything else that I did is what I've done for years. I used the bundle and got the best visible progress in my waist I've ever seen."</p></article>
    <div class="arrows" style="top:163px"><span>←</span><span>→</span></div>
  </section>
</main>

<main class="column col-right">

  <section class="section" style="top:0;height:268px;background:var(--lav)">
    <div class="a c h2" style="top:14px">What to Expect<br><span class="hl">When Taking Vital Prime Daily</span></div>
    <div class="rule" style="top:46px"></div>
    <div class="a c" style="top:52px;font-size:4.5px;font-weight:500">Here's what you can expect over <span class="hl" style="font-size:6px">three months</span> of regular use:</div>
    <div class="card-month" style="top:79px;height:41px;background:var(--blue-soft)"><div class="badge">After<span>Month</span><span>1</span></div><h4>Reduced Hunger and Cravings for Carbs and Sugar</h4><p>Participants in a clinical study showed decreased hunger and reduced sugar cravings after 4-8 weeks*</p></div>
    <div class="card-month" style="top:136px;height:41px;background:var(--blue-mid)"><div class="badge">After<span>Month</span><span>2</span></div><h4>Healthy Fat Loss and Reduction in Body Weight</h4><p>Participants in a clinical study showed a reduction in body weight, visceral fat and hip and waist circumference, with a healthy lifestyle*</p></div>
    <div class="card-month" style="top:192px;height:45px;background:var(--blue-deep)"><div class="badge">After<span>Month</span><span>3</span></div><h4>Increased GLP-1 Levels and Healthy Blood Sugar Levels</h4><p>Participants in a 12-week clinical study using Citrolin® lemon bioflavonoid complex showed increased GLP-1 levels and healthy blood sugar levels within the normal range*</p></div>
  </section>

  <section class="section" style="top:268px;height:185px">
    <div class="a" style="left:128px;top:50px;width:100px;height:100px;border-radius:50%;background:radial-gradient(circle,#fff 35%,#c8cff9 60%,#eef0fc 61%,#fff 70%)"></div>
    <div class="a" role="img" aria-label="Three supplement bottles: Vital Prime Daily, Liver Prime and Tummy Prime" style="left:116px;top:70px;width:86px;height:44px;border-radius:5px;background:linear-gradient(90deg,#e6e9fb 33%,#d33b83 34%,#f3f3f3 66%,#d92b3a 67%)"></div>
    <div class="a c h2" style="top:9px;line-height:1.3">Want Faster Weight Loss?<br><span class="hl">Try the Complete Weight Loss Bundle!</span></div>
    <div class="rule" style="top:34px"></div>
    <div class="a c p" style="top:39px;padding:0 30px;font-size:2.8px;color:var(--ink)">While Vital Prime Daily provides powerful support for blood sugar balance, combining it with our full Weight Loss Bundle takes your results to the next level.</div>
    <div class="a list-title" style="left:12px;top:55px;font-size:4.8px">The Weight Loss Bundle includes:</div>
    <div class="item p" style="left:12px;top:67px;width:96px;font-size:2.8px"><span class="hl" style="font-size:3.8px">Liver Prime</span> – A liver detox that accelerates fat burning in the body and supports liver health</div>
    <div class="item p" style="left:12px;top:80px;width:96px;font-size:2.8px"><span class="hl" style="font-size:3.8px">Tummy Prime</span> – Improves digestion, promotes regularity, reduces bloating and supports gut health</div>
    <div class="item p" style="left:12px;top:93px;width:96px;font-size:2.8px"><span class="hl" style="font-size:3.8px">Vital Prime Daily</span> – Supports fat loss, reduces craving and stabilizes blood sugar</div>
    <div class="a p" style="left:12px;top:110px;width:100px;font-size:2.8px;color:var(--ink)">Why bundle? These three products work synergistically to reset your metabolism, eliminate waste, and keep your body in fat-burning mode. Bundle &amp; Save! Get all three at a discounted price for full-body support.</div>
    <div class="btn" style="left:41px;top:141px;width:121px;height:13px;font-size:3.5px">UPGRADE TO THE WEIGHT LOSS BUNDLE &amp; SAVE NOW!</div>
  </section>

  <section class="section" style="top:453px;height:187px">
    <div class="photo" role="img" aria-label="Smiling woman holding a bottle" style="left:-40px;top:36px;width:118px;height:136px;border-radius:50%;border:3px solid #c3cbf7;background:linear-gradient(160deg,#7c6556,#2a1f1a)"></div>
    <div class="a h2" style="left:89px;top:12px;font-size:9px">Frequently Asked<br><span class="hl">Questions</span></div>
    <div class="a" style="left:89px;top:36px;width:22px;height:1px;background:var(--blue)"></div>
    <div class="a" style="left:90px;top:45px;width:95px;height:68px;border:.5px solid var(--lav-2);background:#fff">
      <div style="background:var(--blue);color:#fff;font-size:2.5px;padding:1.8px 3px;height:7px">01&nbsp;&nbsp;What are the benefits of Vital Prime Daily?</div>
      <p style="font-size:2.1px;line-height:1.45;color:var(--muted);padding:2px 3px">Vital Prime Daily is a dietary supplement that will help you maintain your health, weight and energy naturally. It is for those who want healthy fat loss and reduction in body weight, including visceral (belly) fat, when combined with a healthy lifestyle. It also increases GLP-1 levels which help you feel full longer so you eat less. This will help control hunger and reduce cravings. It stabilizes blood sugar levels to prevent your body from storing fat and to reduce food cravings for carbs and sugar. It also helps to maintain blood glucose levels within the normal range, help support normal insulin sensitivity and help manage a healthy inflammation response.</p>
    </div>
    <div class="faq-row" style="top:117px">02&nbsp;&nbsp;Can Vital Prime Daily help with belly fat?</div>
    <div class="faq-row" style="top:127px">03&nbsp;&nbsp;Can Vital Prime Daily be taken with Liver Prime?</div>
    <div class="faq-row" style="top:137px">04&nbsp;&nbsp;How many do you take daily?</div>
    <div class="faq-row" style="top:147px">05&nbsp;&nbsp;Who is Vital Prime Daily for?</div>
    <div class="faq-row" style="top:157px">06&nbsp;&nbsp;Vital Prime Daily features Citrolin®, what is this ingredient?</div>
    <div class="faq-row" style="top:167px">07&nbsp;&nbsp;What are the ingredients for Vital Prime Daily?</div>
  </section>

  <section class="section on-blue" style="top:640px;height:133px">
    <div class="photo" role="img" aria-label="Smiling woman in white top holding a bottle" style="left:118px;top:-20px;width:85px;height:153px;border-radius:0;background:linear-gradient(180deg,#2a1f1a 20%,#8d6d5b 35%,#f2f2f2 45%,#1b1b22 75%)"></div>
    <div class="a" style="left:11px;top:10px;font-size:9px;font-weight:500;line-height:1.25;z-index:2">Still Unsure if Vital Prime<br>Daily is Right for You?</div>
    <div class="a p" style="left:11px;top:42px;width:95px;font-size:2.8px">We understand that choosing the right supplement is a big decision. If you're still on the fence, why not give Vital Prime Daily a try with confidence?</div>
    <div class="a" style="left:11px;top:60px;font-size:5.2px">Here's the best part</div>
    <div class="a" style="left:11px;top:68px;font-size:6px;font-style:italic">Subscribe today and get</div>
    <div class="a" style="left:11px;top:79px;font-size:5.6px"><span style="font-size:9px;font-weight:500">10% OFF</span> your first order!</div>
    <div class="a p" style="left:11px;top:93px;width:80px;font-size:2.8px">Take the first step toward balanced blood sugar stable energy, and effortless weight loss</div>
    <div class="btn" style="left:11px;top:104px;width:47px;height:13px;background:var(--navy);font-size:3.4px">ORDER NOW</div>
    <div class="a" role="img" aria-label="Guarantee seal" style="left:89px;top:87px;width:44px;height:44px;border-radius:50%;background:var(--gold);border:2px solid #1b1b28"></div>
  </section>

  <section class="section" style="top:773px;height:106px;background:var(--lav)">
    <div class="a c h2" style="top:20px;font-size:9px">Customer Reviews</div>
    <div class="rule" style="top:35px"></div>
    <div class="a c" style="top:58px;font-size:7px;color:#b5b8cc">SPACE for REVULA Reviews</div>
  </section>

  <footer class="section" style="top:879px;height:67px">
    <div class="a c logo" style="top:10px;font-size:6.5px">KPLARE</div>
    <div class="a" style="left:42px;top:29px;width:4px;height:4px;background:var(--blue);border-radius:1px"></div>
    <div class="a" style="left:49px;top:28px;font-size:2px;line-height:1.4">CALL US<br>0012 345 6789</div>
    <div class="a" style="left:76px;top:29px;width:4px;height:4px;background:var(--blue);border-radius:1px"></div>
    <div class="a" style="left:83px;top:28px;font-size:2px;line-height:1.4">EMAIL US<br>info@kplarewellness.com</div>
    <div class="a" style="left:118px;top:29px;width:4px;height:4px;background:var(--blue);border-radius:1px"></div>
    <div class="a" style="left:125px;top:28px;font-size:2px;line-height:1.4">Address line Dummy Here<br>Address line Here</div>
    <div class="a" style="left:12px;top:44px;width:179px;height:.5px;background:#d6d8e4"></div>
    <div class="a c" style="top:48px;font-size:2.1px;word-spacing:10px">HOME SUCCESS&nbsp;STORIES MEDIA&nbsp;ROOM ABOUT BLOGS CONTACT&nbsp;US</div>
    <div class="a" style="left:0;top:59px;width:203px;height:8px;background:var(--blue)">
      <span class="a" style="left:12px;top:2.6px;font-size:1.8px;color:#fff">Copyright © 2025 All Rights Reserved by Company name</span>
      <span class="a" style="left:173px;top:2px;width:4px;height:4px;border:.4px solid #fff;border-radius:1px"></span>
      <span class="a" style="left:178px;top:2px;width:4px;height:4px;border:.4px solid #fff;border-radius:1px"></span>
      <span class="a" style="left:183px;top:2px;width:4px;height:4px;border:.4px solid #fff;border-radius:1px"></span>
      <span class="a" style="left:188px;top:2px;width:4px;height:4px;border:.4px solid #fff;border-radius:1px"></span>
    </div>
  </footer>
</main>

</body>
</html>
```